Alterations to existing business card

Here is my current logo and I want the "cafe and bar" taken off with just the words Lumo and our slogan "Savour every sip" on the card, Plus the logo.
Our Current Business Card is currently 5.5cm by 5.5cm and would like it to remain like this thanks.
The loyalty card can be 10 squares with the logo specifying the 10th coffee free. I would like the cheapest option please.
Also on our business card would like the Facebook logo and instagram Logo with TAZALUMO27 as link to our photos on instagram.

Keep Colour schemes the same please.

On the business cards

Dale Brinton Director
0427916038
dale27lumo@mailvista.test

Paula Ferrisi Principal
0428571963
paulumo@mailvista.test

Thanks Dale

Industry/Entity Type

Business

```html
<!DOCTYPE html>
<html lang="en">
<head>
<meta charset="utf-8">
<title>Lumo – Business Card and Loyalty Card</title>
<link rel="stylesheet" href="https://fonts.googleapis.com/css2?family=Questrial&display=swap">
<style>
  :root {
    --backdrop: #4a4a4a;
    --card-white: #ffffff;
    --ink: #0a0a0a;
    --gold: #f0b030;
    --gold-deep: #e8a22a;
    --gold-light: #f9df74;
    --stamp-free: #f0a232;
    --text-light: #ffffff;
  }
  html, body {
    margin: 0;
    padding: 0;
    width: 1105px;
    height: 1200px;
    overflow: hidden;
    background: var(--backdrop);
    font-family: "Questrial", "Century Gothic", sans-serif;
  }
  .canvas {
    position: relative;
    width: 1105px;
    height: 1200px;
  }
  .card {
    position: absolute;
    width: 449px;
    height: 449px;
    display: block;
  }
  .card--business { left: 124px; top: 110px; }
  .card--loyalty { left: 500px; top: 628px; }
  .brand-name { font-size: 31px; letter-spacing: 1px; fill: var(--ink); }
  .slogan { font-size: 8.5px; letter-spacing: 1.2px; fill: var(--gold-deep); }
  .person-name { font-size: 19px; letter-spacing: 1px; fill: var(--gold); }
  .person-role { font-size: 13px; letter-spacing: 0.5px; fill: var(--text-light); }
  .contact { font-size: 13.5px; fill: var(--text-light); }
  .loyalty-name { font-size: 26px; letter-spacing: 1px; fill: var(--ink); }
  .stamp-free-label { font-size: 13px; font-weight: 700; fill: var(--ink); }
  .social-handle { font-size: 12.5px; letter-spacing: 0.8px; fill: var(--ink); }
</style>
</head>
<body>
<main class="canvas">

  <svg class="card card--business" viewBox="0 0 325 325" aria-label="Lumo business card for Dale Brinton">
    <defs>
      <linearGradient id="goldRing" x1="0" y1="0" x2="1" y2="1">
        <stop offset="0" stop-color="var(--gold-light)"/>
        <stop offset="1" stop-color="var(--gold-deep)"/>
      </linearGradient>
      <clipPath id="businessClip"><rect width="325" height="325"/></clipPath>
    </defs>
    <rect class="card-face" width="325" height="325" fill="var(--card-white)"/>

    <g class="brand-lockup">
      <circle class="brand-circle" cx="162.5" cy="68" r="40" fill="none" stroke="url(#goldRing)" stroke-width="2.5"/>
      <text class="brand-name" x="162.5" y="140" text-anchor="middle">LUMO</text>
      <text class="slogan" x="162.5" y="151" text-anchor="middle">SAVOUR EVERY SIP</text>
    </g>

    <g class="contact-band" clip-path="url(#businessClip)">
      <circle cx="162.5" cy="410" r="243" fill="none" stroke="var(--ink)" stroke-width="3"/>
      <circle cx="162.5" cy="410" r="238.5" fill="none" stroke="var(--gold)" stroke-width="5"/>
      <circle cx="162.5" cy="410" r="236" fill="var(--ink)"/>
      <circle cx="162.5" cy="410" r="229" fill="none" stroke="var(--gold)" stroke-width="1.2"/>
    </g>

    <text class="person-name" x="162.5" y="231" text-anchor="middle">DALE BRINTON</text>
    <text class="person-role" x="162.5" y="253" text-anchor="middle">DIRECTOR</text>
    <text class="contact" x="162.5" y="281" text-anchor="middle">0427916038</text>
    <text class="contact" x="162.5" y="301" text-anchor="middle">dale27lumo@mailvista.test</text>
  </svg>

  <svg class="card card--loyalty" viewBox="0 0 325 325" aria-label="Lumo coffee loyalty card">
    <defs>
      <linearGradient id="loyaltyFace" x1="0" y1="0" x2="1" y2="0">
        <stop offset="0" stop-color="var(--gold-deep)"/>
        <stop offset="0.55" stop-color="#f5c24a"/>
        <stop offset="1" stop-color="var(--gold-light)"/>
      </linearGradient>
      <symbol id="coffeeCup" viewBox="0 0 24 24">
        <path d="M4 10h13v3a6 6 0 0 1-6 6h-1a6 6 0 0 1-6-6z" fill="var(--ink)"/>
        <path d="M17 11.5h1.5a2.2 2.2 0 0 1 0 4.4H16.5" fill="none" stroke="var(--ink)" stroke-width="1.4"/>
        <rect x="2.5" y="19.8" width="16" height="1.4" rx="0.7" fill="var(--ink)"/>
        <path d="M8.5 8c-1-1.2 1-2 0-3.4M11.5 8c-1-1.2 1-2 0-3.4" fill="none" stroke="var(--ink)" stroke-width="0.9"/>
      </symbol>
      <symbol id="stampRing" viewBox="0 0 46 46">
        <circle cx="23" cy="23" r="21.5" fill="none" stroke="var(--ink)" stroke-width="2"/>
        <circle cx="23" cy="23" r="18.5" fill="none" stroke="var(--ink)" stroke-width="0.8"/>
      </symbol>
    </defs>
    <rect class="card-face" width="325" height="325" fill="url(#loyaltyFace)"/>

    <g class="brand-lockup">
      <circle class="brand-circle" cx="162" cy="93" r="58" fill="none" stroke="var(--ink)" stroke-width="2.5"/>
      <text class="loyalty-name" x="162" y="102" text-anchor="middle">LUMO</text>
    </g>

    <g class="stamp-grid">
      <use href="#stampRing" x="27" y="164" width="46" height="46"/><use href="#coffeeCup" x="39" y="174" width="24" height="24"/>
      <use href="#stampRing" x="80" y="164" width="46" height="46"/><use href="#coffeeCup" x="92" y="174" width="24" height="24"/>
      <use href="#stampRing" x="133" y="164" width="46" height="46"/><use href="#coffeeCup" x="145" y="174" width="24" height="24"/>
      <use href="#stampRing" x="185" y="164" width="46" height="46"/><use href="#coffeeCup" x="197" y="174" width="24" height="24"/>
      <use href="#stampRing" x="238" y="164" width="46" height="46"/><use href="#coffeeCup" x="250" y="174" width="24" height="24"/>

      <use href="#stampRing" x="27" y="224" width="46" height="46"/><use href="#coffeeCup" x="39" y="234" width="24" height="24"/>
      <use href="#stampRing" x="80" y="224" width="46" height="46"/><use href="#coffeeCup" x="92" y="234" width="24" height="24"/>
      <use href="#stampRing" x="133" y="224" width="46" height="46"/><use href="#coffeeCup" x="145" y="234" width="24" height="24"/>
      <use href="#stampRing" x="185" y="224" width="46" height="46"/><use href="#coffeeCup" x="197" y="234" width="24" height="24"/>

      <g class="stamp stamp--free">
        <circle cx="261" cy="247" r="22" fill="var(--stamp-free)" stroke="var(--ink)" stroke-width="1.5"/>
        <text class="stamp-free-label" x="261" y="252" text-anchor="middle">FREE</text>
      </g>
    </g>

    <g class="social-line">
      <line x1="40" y1="296" x2="106" y2="296" stroke="var(--ink)" stroke-width="0.8"/>
      <circle cx="117" cy="296" r="6" fill="var(--ink)"/>
      <text class="social-handle" x="128" y="300.5">TAZALUMO27</text>
      <line x1="220" y1="296" x2="286" y2="296" stroke="var(--ink)" stroke-width="0.8"/>
    </g>
  </svg>

</main>
</body>
</html>
```